Company director needs a business card design

I am a semi-retired former senior finance executive who sits on a number of public and private company boards and do some consulting work. I work largely with emerging businesses but deal regularly with top end of town lawyers, bankers etc. I need a thoughtful but relatively conservative design which would also resonate with my younger client base. Some colour would be good. Information limited to name, address, office tel, mobile and email.

Finance

```html
<!DOCTYPE html>
<html lang="en">
<head>
<meta charset="utf-8">
<title>Director Business Card</title>
<link rel="stylesheet" href="https://fonts.googleapis.com/css2?family=Cinzel:wght@400&family=Jost:wght@400&display=swap">
<style>
  :root {
    --stage: #e9e9eb;
    --card: #ffffff;
    --ink: #111111;
    --leaf: #5fba47;
    --forest: #12a04a;
    --band-black: #000000;
  }
  * { margin: 0; padding: 0; box-sizing: border-box; }
  html, body {
    width: 1200px;
    height: 864px;
    overflow: hidden;
    background: var(--stage);
  }
  .stage {
    position: relative;
    width: 1200px;
    height: 864px;
    display: flex;
    align-items: center;
    justify-content: center;
  }
  .business-card {
    position: relative;
    width: 900px;
    height: 514px;
    background: var(--card);
    overflow: hidden;
    box-shadow: 0 10px 30px rgba(0,0,0,0.12);
  }
  .card-bands {
    position: absolute;
    inset: 0;
    width: 900px;
    height: 514px;
  }
  .holder-name {
    position: absolute;
    left: 82px;
    top: 62px;
    font-family: "Cinzel", serif;
    font-size: 36px;
    font-weight: 400;
    color: var(--ink);
    letter-spacing: 0.5px;
    white-space: nowrap;
  }
  .contact-list {
    position: absolute;
    left: 80px;
    top: 162px;
    list-style: none;
    font-family: "Jost", sans-serif;
    font-size: 25px;
    line-height: 30px;
    color: var(--ink);
  }
  .contact-item {
    display: flex;
    align-items: center;
    margin-bottom: 14px;
    white-space: nowrap;
  }
  .contact-icon {
    width: 22px;
    height: 24px;
    margin-right: 46px;
    flex: none;
    fill: var(--ink);
  }
</style>
</head>
<body>
<main class="stage">
  <article class="business-card">
    <svg class="card-bands" viewBox="0 0 900 514" aria-hidden="true">
      <path fill="var(--forest)" d="M690 400 C770 355 860 300 900 240 L900 300 C850 340 770 380 725 400 Z"/>
      <path fill="var(--leaf)" d="M0 400 L720 400 C780 370 860 320 900 280 L900 455 L0 455 Z"/>
      <rect fill="var(--band-black)" x="0" y="455" width="900" height="59"/>
    </svg>

    <h1 class="holder-name">Your Name</h1>

    <ul class="contact-list">
      <li class="contact-item">
        <svg class="contact-icon" viewBox="0 0 24 24" aria-label="Office"><path d="M6.6 10.8c1.4 2.8 3.8 5.1 6.6 6.6l2.2-2.2c.3-.3.7-.4 1-.2 1.1.4 2.3.6 3.6.6.6 0 1 .4 1 1V20c0 .6-.4 1-1 1C10.6 21 3 13.4 3 4c0-.6.4-1 1-1h3.5c.6 0 1 .4 1 1 0 1.3.2 2.5.6 3.6.1.3 0 .7-.2 1z"/></svg>
        <span>+1 (555) 0142 376</span>
      </li>
      <li class="contact-item">
        <svg class="contact-icon" viewBox="0 0 24 24" aria-label="Mobile"><path d="M7 1h10a2 2 0 0 1 2 2v18a2 2 0 0 1-2 2H7a2 2 0 0 1-2-2V3a2 2 0 0 1 2-2zm0 3v15h10V4zm5 16.2a.9.9 0 1 0 0 1.8.9.9 0 0 0 0-1.8z"/></svg>
        <span>+1 (555) 0198 624</span>
      </li>
      <li class="contact-item">
        <svg class="contact-icon" viewBox="0 0 24 24" aria-label="Address"><path d="M12 1a7.5 7.5 0 0 0-7.5 7.5C4.5 14 12 23 12 23s7.5-9 7.5-14.5A7.5 7.5 0 0 0 12 1z"/></svg>
        <span>48 Harbor Lane, Millbrook, NY 10045<br>P.O. Box: 407251</span>
      </li>
      <li class="contact-item">
        <svg class="contact-icon" viewBox="0 0 24 24" aria-label="Email"><path d="M2 6h20v13H2zm1.5 1.5v.4L12 13l8.5-5.1v-.4zm0 2.1v7.9h17V9.6L12 14.7z"/></svg>
        <span>desk@northmail.com</span>
      </li>
    </ul>
  </article>
</main>
</body>
</html>
```